2 x Digitize Logo | 2 x Business Cards | 2 x Fridge Magnets

We require 6 deliverables:
1. Residential logo redrawn (same just high quality for large print format).
2. Corporate logo redrawn (minor changes to wording and high quality for large print format).
3. New business card design for Furniture Removals (residential)
4. New business card design for Corporate Relocations (business)
5. New Fridge magnet for Furniture removals (residential)
6. New fridge magnet for Corporate Relocations (business)
1. Residential Logo
a. We require the logo to be translated into a high quality digital image with no modifications.
(see attached resilogo.jpg)
2. Residential Logo
a. We require the logo to be edited (add the word corporate relocations) be translated into a high quality digital image.
(see attached corplogo.jpg)
3. Using the resilogo please make a new business card for our business.
a. Please see the web site https://www.larkbendcarters.com.au for colours and inspiration.
b. The residential business card needs the following information:
i. Business Name (using the residential logo).
ii. Free Call: 1800 LB Cart (the L, B and Cart much be the same colour as the logo).
iii. Website: www.LarkbendCarters.com.au
iv. Address: 4/17 Ormsdale Court, VIC 3264
v. Email: cart@LarkbendCarters.com.au
vi. backof Card:
Review our service
www.PennantOrbit.com.au
Services: Local, Country, Interstate | Furniture Removals | Piano, Billiard Tables & Antiques
4. Using the corplogo please make a new business card for our business.
b. The corporate business card needs the following information:
i. Business Name (using the corporate logo).
v. Email: corporate@LarkbendCarters.com.au
vi. Back of Card:
Review our service
www.PennantOrbit.com.au
Services: Corporate relocations | Office equipment moves | Packing Service | Packing Materials
5. Using the resilogo please make a new fridge magent for our business.
b. The residential fidge magnet needs the following information:
iv. Services: Local, Country, Interstate | Furniture Removals | Piano, Billiard Tables & Antiques
6. Using the corplogo please make a new fridge magent for our business.
b. The corporate fidge magnet needs the following information:
iv. Services: Local, Country, Interstate | Corporate relocations
Target Market(s)
Residential Furniture Removals and Corporate Office relocations
Industry/Entity Type
Business
Contact Information for Business Card
Please see full brief for six items required
Requirements
Must have
- Clean simple, easy to read
Nice to have
- fresh, stand out, eye catching
Should not have
- plain, standard, boring, general

```html
<!DOCTYPE html>
<html lang="en">
<head>
<meta charset="utf-8">
<title>Larkbend Carters – Business Card</title>
<link rel="stylesheet" href="https://fonts.googleapis.com/css2?family=Open+Sans:wght@400;600;700;800&display=swap">
<style>
  :root {
    --green: #22b14c;
    --yellow: #f5c400;
    --red: #e8202a;
    --white: #ffffff;
    --ink: #1a1a1a;
    --backdrop: #ecebe8;
  }
  * { box-sizing: border-box; margin: 0; padding: 0; }
  html, body {
    width: 1109px; height: 1200px; overflow: hidden;
    background: var(--backdrop);
    font-family: "Open Sans", Arial, sans-serif;
  }
  .card {
    position: absolute; left: 124px;
    width: 860px; height: 533px;
    box-shadow: 0 6px 22px rgba(0,0,0,.18);
    overflow: hidden;
  }
  .card--front { top: 44px; background: var(--white); }
  .card--back { top: 623px; background: var(--green); }

  .front-band { position: absolute; inset: 0; }

  .brand-name {
    position: absolute; right: 40px; top: 68px;
    font-size: 44px; font-weight: 800; letter-spacing: .5px;
    color: var(--green); white-space: nowrap;
  }

  .services { position: absolute; left: 46px; top: 336px; color: var(--white); }
  .services__title { font-size: 26px; font-weight: 400; margin-bottom: 18px; }
  .services__list { list-style: none; font-size: 23px; line-height: 31px; }
  .services__list li::before {
    content: ""; display: inline-block; width: 11px; height: 11px;
    border-radius: 50%; background: var(--white);
    margin-right: 9px; vertical-align: 2px;
  }

  .contact {
    position: absolute; right: 32px; top: 350px;
    text-align: right; color: var(--ink); font-size: 22px;
  }
  .contact__line { display: flex; justify-content: flex-end; align-items: center; height: 31px; gap: 8px; }
  .contact__line--address { margin-top: 10px; }
  .contact__icon { width: 18px; height: 18px; flex: none; }
  .free-call .l { color: var(--yellow); font-weight: 700; }
  .free-call .b { color: var(--red); font-weight: 700; }
  .free-call .cart { color: var(--green); font-weight: 700; }

  .review {
    position: absolute; left: 0; right: 0; top: 228px;
    text-align: center;
  }
  .review__label { color: var(--white); font-size: 26px; }
  .review__url { color: var(--red); font-size: 30px; margin-top: 4px; }
</style>
</head>
<body>
  <section class="card card--front">
    <svg class="front-band" viewBox="0 0 860 533" aria-hidden="true">
      <polygon points="0,0 356,0 270,82 455,533 0,533" fill="var(--green)"/>
      <polyline points="356,0 270,82 455,533" fill="none" stroke="var(--yellow)" stroke-width="5"/>
    </svg>

    <div class="brand-name">LARKBEND CARTERS</div>

    <div class="services">
      <h2 class="services__title">SERVICES</h2>
      <ul class="services__list">
        <li>Local, Country, Interstate</li>
        <li>Furniture Removals</li>
        <li>Piano, Billiard Tables &amp; Antiques</li>
      </ul>
    </div>

    <div class="contact">
      <div class="contact__line free-call">
        <span>1800 <span class="l">L</span><span class="b">B</span> <span class="cart">Cart</span> / 1800 52 27 86</span>
        <svg class="contact__icon" viewBox="0 0 24 24"><path fill="var(--green)" d="M6.6 10.8a15.1 15.1 0 0 0 6.6 6.6l2.2-2.2c.3-.3.7-.4 1-.2 1.1.4 2.3.6 3.6.6.6 0 1 .4 1 1V20c0 .6-.4 1-1 1A17 17 0 0 1 3 4c0-.6.4-1 1-1h3.5c.6 0 1 .4 1 1 0 1.3.2 2.5.6 3.6.1.3 0 .7-.2 1z"/></svg>
      </div>
      <div class="contact__line">
        <span>cart@LarkbendCarters.com.au</span>
        <svg class="contact__icon" viewBox="0 0 24 24"><rect x="2" y="5" width="20" height="14" rx="1" fill="var(--green)"/><polyline points="3,6 12,13 21,6" fill="none" stroke="var(--white)" stroke-width="1.8"/></svg>
      </div>
      <div class="contact__line">
        <span>www.LarkbendCarters.com.au</span>
        <svg class="contact__icon" viewBox="0 0 24 24"><circle cx="12" cy="12" r="10" fill="var(--green)"/><ellipse cx="12" cy="12" rx="4" ry="10" fill="none" stroke="var(--white)" stroke-width="1.5"/><line x1="2" y1="12" x2="22" y2="12" stroke="var(--white)" stroke-width="1.5"/></svg>
      </div>
      <div class="contact__line contact__line--address">
        <span>4/17 Ormsdale Court, VIC 3264</span>
        <svg class="contact__icon" viewBox="0 0 24 24"><path fill="var(--green)" d="M12 2a7 7 0 0 0-7 7c0 5.2 7 13 7 13s7-7.8 7-13a7 7 0 0 0-7-7zm0 9.5A2.5 2.5 0 1 1 12 6.5a2.5 2.5 0 0 1 0 5z"/></svg>
      </div>
    </div>
  </section>

  <section class="card card--back">
    <div class="review">
      <p class="review__label">Review Our Service</p>
      <p class="review__url">www.PennantOrbit.com.au</p>
    </div>
  </section>
</body>
</html>
```